Create a business promotion flyer to leave in customer mailboxes. We are a bulk petroleum supplier, servicing any industry that requires diesel. Base in griffith NSW, servicing griffith area and surrounds.

Business Name - Terra Diesel
Fuel@terradiesel-example.com.au
Owen - 0491 570 362 ohartley@terradiesel-example.com.au
Liam - 0491 570 718 lprosser@terradiesel-example.com.au
Simon - 0491 570 905 skenway@terradiesel-example.com.au
Office 02 5550 1734

Bulk Fuel deliveries.
Oils & lubricants
Local Family owned business

```html
<!DOCTYPE html>
<html lang="en">
<head>
<meta charset="utf-8">
<title>Terra Diesel – Bulk Diesel Supply</title>
<link href="https://fonts.googleapis.com/css2?family=Inter:wght@400;500&family=Roboto:wght@700;900&display=swap" rel="stylesheet">
<style>
  :root {
    --red: #ee2a1e;
    --red-deep: #981812;
    --grey-panel: #e4e4e4;
    --grey-edge: #8c8c8c;
    --carbon: #1f1f1f;
    --carbon-light: #3a3a3a;
    --white: #ffffff;
    --ink: #111111;
    --map-fill: #cd716b;
  }
  * { margin: 0; padding: 0; box-sizing: border-box; }
  html, body { width: 927px; height: 1200px; overflow: hidden; background: var(--white); }
  .flyer { position: relative; width: 927px; height: 1200px; overflow: hidden; font-family: "Inter", sans-serif; color: var(--ink); background: var(--white); }

  .carbon { background: linear-gradient(135deg, var(--carbon-light), var(--carbon) 50%, var(--carbon-light)); }

  /* header */
  .header-band { position: absolute; left: 0; top: 0; width: 927px; height: 206px; background: var(--red); }
  .header-carbon { position: absolute; left: 0; top: 0; width: 927px; height: 127px; clip-path: polygon(763px 0, 927px 0, 927px 127px, 681px 127px); }
  .header-edge { position: absolute; left: 0; top: 0; width: 927px; height: 127px; background: var(--grey-edge); clip-path: polygon(756px 0, 765px 0, 683px 127px, 674px 127px); }
  .header-rule { position: absolute; left: 0; top: 206px; width: 927px; height: 8px; background: var(--grey-edge); }
  .intro-panel { position: absolute; left: 0; top: 214px; width: 927px; height: 242px; background: var(--grey-panel); }

  .brand-pill { position: absolute; left: 36px; top: 36px; width: 324px; height: 121px; border-radius: 61px; background: var(--white); display: flex; align-items: center; justify-content: center; gap: 12px; }
  .brand-mark { width: 20px; height: 20px; border-radius: 50%; background: var(--red); }
  .brand-name { font-family: "Inter", sans-serif; font-weight: 500; font-size: 34px; color: var(--red); letter-spacing: -0.5px; }

  .headline { position: absolute; left: 36px; top: 247px; font-family: "Roboto", sans-serif; font-weight: 900; font-size: 50px; line-height: 58px; color: var(--red); letter-spacing: -0.5px; }

  .hero-frame { position: absolute; left: 362px; top: 127px; width: 580px; height: 329px; background: var(--white); border-radius: 170px 0 0 170px; }
  .hero-photo { position: absolute; left: 371px; top: 136px; width: 570px; height: 312px; border-radius: 162px 0 0 162px; background: linear-gradient(180deg, #4f86c9 0%, #a9c6e6 38%, #eceff2 55%, #c9cbcd 78%, #b9b8b4 100%); }

  /* services */
  .strip-top { position: absolute; left: 0; top: 456px; width: 927px; height: 14px; }
  .services { position: absolute; left: 0; top: 470px; width: 927px; height: 327px; background: radial-gradient(ellipse at 50% 20%, var(--red) 0%, #c8201a 45%, var(--red-deep) 100%); }
  .service-list { position: absolute; left: 36px; top: 521px; list-style: none; }
  .service { position: absolute; left: 0; display: flex; align-items: center; width: 400px; }
  .service-icon { width: 61px; height: 61px; border-radius: 50%; background: var(--white); display: flex; align-items: center; justify-content: center; flex: none; }
  .service-text { margin-left: 30px; font-size: 26px; line-height: 33px; color: var(--white); }
  .divider { position: absolute; left: 463px; top: 530px; width: 2px; height: 206px; background: rgba(255,255,255,0.75); }

  .region-map { position: absolute; left: 609px; top: 505px; width: 192px; height: 148px; background: var(--map-fill); border: 2px solid var(--white); }
  .region-label { position: absolute; left: 609px; top: 549px; width: 192px; text-align: center; font-size: 27px; color: var(--white); }
  .region-text { position: absolute; left: 540px; top: 658px; width: 378px; text-align: center; font-size: 24px; line-height: 33px; color: var(--white); }

  /* contacts */
  .strip-mid { position: absolute; left: 0; top: 797px; width: 927px; height: 30px; }
  .contact-tab { position: absolute; left: 0; top: 780px; width: 400px; height: 48px; background: var(--white); clip-path: polygon(0 0, 341px 0, 388px 48px, 0 48px); }
  .contact-title { position: absolute; left: 68px; top: 798px; font-family: "Roboto", sans-serif; font-weight: 700; font-size: 28px; color: var(--red); }

  .team { position: absolute; left: 0; top: 870px; width: 927px; display: flex; justify-content: space-between; padding: 0 0 0 14px; }
  .member { position: absolute; top: 870px; width: 310px; text-align: center; }
  .member-photo { width: 136px; height: 136px; margin: 0 auto; }
  .member-name { margin-top: 12px; font-size: 22px; line-height: 28px; }
  .member-phone { margin-top: 3px; font-size: 18px; line-height: 24px; }
  .member-email { margin-top: 5px; font-size: 14.5px; line-height: 20px; }

  /* footer */
  .footer { position: absolute; left: 0; top: 1119px; width: 927px; height: 81px; }
  .footer-edge { position: absolute; left: 0; top: 1119px; width: 927px; height: 81px; background: var(--grey-edge); clip-path: polygon(0 0, 581px 0, 485px 81px, 0 81px); }
  .footer-red { position: absolute; left: 0; top: 1119px; width: 927px; height: 81px; background: var(--red); clip-path: polygon(0 0, 568px 0, 472px 81px, 0 81px); }
  .office { position: absolute; left: 37px; top: 1140px; font-family: "Roboto", sans-serif; font-weight: 700; font-size: 31px; line-height: 40px; color: var(--white); letter-spacing: 0.5px; }
  .footer-email { position: absolute; right: 38px; top: 1147px; font-size: 19px; line-height: 26px; color: var(--white); }
</style>
</head>
<body>
<main class="flyer">
  <header>
    <div class="header-band"></div>
    <div class="header-carbon carbon"></div>
    <div class="header-edge"></div>
    <div class="header-rule"></div>
    <div class="intro-panel"></div>
    <div class="brand-pill">
      <span class="brand-mark"></span>
      <span class="brand-name">Terra Diesel</span>
    </div>
    <h1 class="headline">RELIABLE<br>BULK DIESEL<br>SUPPLY.</h1>
    <div class="hero-frame"></div>
    <div class="hero-photo" role="img" aria-label="Photo of a white Terra Diesel road-train fuel tanker parked outside a steel warehouse under a blue, cloudy sky"></div>
  </header>

  <section class="services-block">
    <div class="strip-top carbon"></div>
    <div class="services"></div>
    <ul class="service-list">
      <li class="service" style="top:0">
        <span class="service-icon">
          <svg width="40" height="24" viewBox="0 0 40 24" aria-hidden="true">
            <rect x="0" y="2" width="26" height="15" fill="#ee2a1e"/>
            <path d="M27 6h7l5 6v5H27z" fill="#ee2a1e"/>
            <rect x="29" y="8" width="5" height="4" fill="#fff"/>
            <circle cx="7" cy="20" r="3.2" fill="#ee2a1e" stroke="#fff" stroke-width="1.2"/>
            <circle cx="15" cy="20" r="3.2" fill="#ee2a1e" stroke="#fff" stroke-width="1.2"/>
            <circle cx="33" cy="20" r="3.2" fill="#ee2a1e" stroke="#fff" stroke-width="1.2"/>
          </svg>
        </span>
        <span class="service-text">Bulk Fuel Deliveries.</span>
      </li>
      <li class="service" style="top:80px">
        <span class="service-icon">
          <svg width="28" height="32" viewBox="0 0 28 32" aria-hidden="true">
            <rect x="2" y="1" width="24" height="30" rx="2" fill="#ee2a1e"/>
            <rect x="0" y="7" width="28" height="2.5" fill="#ee2a1e"/>
            <rect x="0" y="22.5" width="28" height="2.5" fill="#ee2a1e"/>
            <path d="M14 10c3 4 5 6 5 8.5a5 5 0 0 1-10 0c0-2.5 2-4.5 5-8.5z" fill="#fff"/>
          </svg>
        </span>
        <span class="service-text">Oils &amp; Lubricants.</span>
      </li>
      <li class="service" style="top:161px">
        <span class="service-icon">
          <svg width="32" height="30" viewBox="0 0 32 30" aria-hidden="true">
            <path d="M16 2L2 14h4v14h8v-8h4v8h8V14h4z" fill="#ee2a1e"/>
          </svg>
        </span>
        <span class="service-text">Local Family-owned<br>business.</span>
      </li>
    </ul>
    <div class="divider"></div>
    <div class="region-map" role="img" aria-label="Outline map of New South Wales marking Griffith"></div>
    <p class="region-label">Griffith</p>
    <p class="region-text">Based in Griffith, NSW.<br>Servicing Griffith Area and<br>Surrounds.</p>
  </section>

  <section class="contacts">
    <div class="strip-mid carbon"></div>
    <div class="contact-tab"></div>
    <h2 class="contact-title">GET IN TOUCH</h2>

    <article class="member" style="left:14px">
      <div class="member-photo" role="img" aria-label="Portrait photo of Owen Hartley" style="background:linear-gradient(180deg,#8fa08a,#5b6a78)"></div>
      <p class="member-name">Owen Hartley</p>
      <p class="member-phone">0491 570 362</p>
      <p class="member-email">ohartley@terradiesel-example.com.au</p>
    </article>
    <article class="member" style="left:322px">
      <div class="member-photo" role="img" aria-label="Portrait photo of Liam Prosser" style="background:linear-gradient(180deg,#d9d2c6,#5e646b)"></div>
      <p class="member-name">Liam Prosser</p>
      <p class="member-phone">0491 570 718</p>
      <p class="member-email">lprosser@terradiesel-example.com.au</p>
    </article>
    <article class="member" style="left:617px">
      <div class="member-photo" role="img" aria-label="Portrait photo of Simon Kenway" style="background:linear-gradient(180deg,#cfd2cf,#e8c46a)"></div>
      <p class="member-name">Simon Kenway</p>
      <p class="member-phone">0491 570 905</p>
      <p class="member-email">skenway@terradiesel-example.com.au</p>
    </article>
  </section>

  <footer>
    <div class="footer carbon"></div>
    <div class="footer-edge"></div>
    <div class="footer-red"></div>
    <p class="office">OFFICE: 02 5550 1734</p>
    <p class="footer-email">Fuel@terradiesel-example.com.au</p>
  </footer>
</main>
</body>
</html>
```